Maple Grove Youngsters Guild Business Card Project

We are a Minneapolis based discount club that caters to families with children. We need a business card that can be used to communicate our contact information to other businesses that may wish to offer discounts on our website.

Please use placeholders for contact information (i.e. John Doe, 123 Any Street, Any Town, etc.) and include spaces for the following: Full name, title, email, phone number, website, one line street address, city, state, and zip code.
Updates

Project Deadline Extended
Reason: I have extended the deadline because I had not intended the project to close so quickly.

Target Market(s)

Most of the time the business cards will be used in business to business situations. However, from time to time they may be distributed to our end customer, families with children.

Industry/Entity Type

Club

Font styles to use
Serif
Sans Serif
Other font styles liked:
• Open to suggestions

Requirements
Nice to have
• We might use the reverse side of the card as the design for our membership card.

```html
<!DOCTYPE html>
<html lang="en">
<head>
<meta charset="utf-8">
<title>Maple Grove Youngsters Guild – Business Card</title>
<link rel="stylesheet" href="https://fonts.googleapis.com/css2?family=Open+Sans:wght@400;700&family=Quicksand:wght@400&display=swap">
<style>
  :root {
    --backdrop: #e9ecec;
    --paper: #ffffff;
    --navy: #1b2a6b;
    --orange: #f48b1f;
    --green: #7cbd3a;
    --red: #a8151f;
    --ink-light: #ffffff;
  }
  * { box-sizing: border-box; margin: 0; padding: 0; }
  html, body {
    width: 1200px; height: 720px; overflow: hidden;
    background: var(--backdrop);
    font-family: "Open Sans", Arial, sans-serif;
  }
  .sheet {
    width: 1200px; height: 720px;
    display: flex; align-items: center; justify-content: center; gap: 40px;
  }
  .card {
    position: relative;
    width: 540px; height: 309px;
    background: var(--paper);
    box-shadow: 0 2px 6px rgba(0,0,0,.12);
    overflow: hidden;
  }
  /* Front */
  .card-front { display: flex; align-items: center; justify-content: center; }
  .brand { display: flex; align-items: center; gap: 14px; }
  .brand-dot { width: 34px; height: 34px; border-radius: 50%; background: var(--orange); flex: none; }
  .brand-name {
    font-weight: 700; font-size: 30px; line-height: 1.1; color: var(--navy);
    max-width: 340px;
  }
  /* Back */
  .identity {
    position: absolute; left: 0; right: 0; top: 92px;
    text-align: center; font-family: "Quicksand", "Century Gothic", sans-serif; color: var(--navy);
  }
  .identity-name { font-size: 40px; font-weight: 400; letter-spacing: .5px; }
  .identity-title { font-size: 20px; margin-top: -4px; padding-left: 70px; }
  .contact-band {
    position: absolute; left: 0; right: 0; bottom: 0; height: 90px;
    display: flex;
  }
  .contact-item {
    display: flex; flex-direction: column; align-items: center; justify-content: center;
    gap: 6px; color: var(--ink-light); font-size: 13px; line-height: 1.35; text-align: center;
  }
  .contact-address { background: var(--orange); flex: 38; }
  .contact-phone { background: var(--green); flex: 27; }
  .contact-web { background: var(--red); flex: 35; }
  .contact-icon { width: 16px; height: 16px; }
</style>
</head>
<body>
<main class="sheet">
  <section class="card card-front" aria-label="Card front">
    <div class="brand">
      <span class="brand-dot"></span>
      <span class="brand-name">Maple Grove Youngsters Guild</span>
    </div>
  </section>

  <section class="card card-back" aria-label="Card back">
    <div class="identity">
      <p class="identity-name">John Doe</p>
      <p class="identity-title">Manager</p>
    </div>
    <div class="contact-band">
      <div class="contact-item contact-address">
        <svg class="contact-icon" viewBox="0 0 16 16" aria-hidden="true"><path d="M8 2 1 8h2v6h4v-4h2v4h4V8h2z" fill="#fff"/></svg>
        <span>48 Birch Lane Maple Grove<br>MN, 55369</span>
      </div>
      <div class="contact-item contact-phone">
        <svg class="contact-icon" viewBox="0 0 16 16" aria-hidden="true"><path d="M3.5 1.5 6 4 4.8 5.6a8 8 0 0 0 5.6 5.6L12 10l2.5 2.5-1.6 2A11 11 0 0 1 1.5 3.1z" fill="#fff"/></svg>
        <span>+1 612 555 0142</span>
      </div>
      <div class="contact-item contact-web">
        <svg class="contact-icon" viewBox="0 0 16 16" aria-hidden="true"><rect x="1.5" y="3.5" width="13" height="9" fill="none" stroke="#fff"/><path d="M1.5 3.5 8 9l6.5-5.5" fill="none" stroke="#fff"/></svg>
        <span>jdoe@youngstersguild.com<br>www.mapleyoungstersguild.com</span>
      </div>
    </div>
  </section>
</main>
</body>
</html>
```